Oil Field Service company needs professional business cards

Looking to clean up our current company business cards and look a little more professional. Brenwick Casing Services is a US based company that services the oil field. We deal with engineers, managers and oil rigs....................................................................................................................................................................................................................................................................................................................................................................................................

Target Market(s)

Oil and Gas professionals

Industry/Entity Type

Oil And Gas

Contact Information for Business Card

See attached photo as example

Font styles to use
Sans Serif

Colors
ec1f27

Requirements
Must have
• Company Logo, Name, Title, Cell, Office, Fax, Email.
• See attached photo
Nice to have
• External CRT, Internal CRT, Casing Crews, Torque Turn, Laydown Machine
Should not have
• Do not introduce any new pictures and keep it professional looking

```html
<!DOCTYPE html>
<html lang="en">
<head>
<meta charset="utf-8">
<title>Brenwick Casing Services – Business Cards</title>
<link rel="stylesheet" href="https://fonts.googleapis.com/css2?family=Oswald:wght@400;500&family=Roboto:wght@400;500;700;900&display=swap">
<style>
  :root {
    --brand-red: #d0201f;
    --slate: #3b5166;
    --ink: #333a40;
    --muted: #555b60;
    --card: #f4f4f3;
    --backdrop: #e2e2e2;
    --rule: #d6d6d6;
  }
  * { margin: 0; padding: 0; box-sizing: border-box; }
  html, body { width: 1200px; height: 576px; overflow: hidden; }
  body { background: var(--backdrop); font-family: "Roboto", Arial, sans-serif; position: relative; }

  .card {
    position: absolute;
    top: 139px;
    width: 484px;
    height: 292px;
    background: var(--card);
    border-radius: 6px;
    overflow: hidden;
    box-shadow: 0 2px 5px rgba(0,0,0,0.25);
  }
  .card--front { left: 81px; }
  .card--back { left: 602px; }

  .wordmark { position: absolute; text-align: center; color: var(--slate); font-family: "Roboto", Arial, sans-serif; font-weight: 900; }
  .wordmark__name { display: block; letter-spacing: 1px; line-height: 1; }
  .wordmark__sub { display: block; letter-spacing: 3px; line-height: 1; }

  .card--front .wordmark { left: 0; right: 0; top: 70px; }
  .card--front .wordmark__name { font-size: 56px; }
  .card--front .wordmark__sub { font-size: 17px; margin-top: 14px; }

  .services-band {
    position: absolute; left: 0; right: 0; top: 220px; height: 27px;
    background: var(--brand-red); color: #fff;
    display: flex; align-items: center; justify-content: center; gap: 8px;
    font-weight: 700; font-size: 12.5px; letter-spacing: 0.2px;
  }
  .services-band .sep { font-weight: 400; }

  .front-web {
    position: absolute; left: 0; right: 0; top: 262px;
    display: flex; align-items: center; justify-content: center; gap: 10px;
    font-size: 13px; color: var(--ink);
  }
  .front-web .dash { width: 66px; height: 2px; background: var(--brand-red); border-radius: 2px; }

  .card--back .wordmark { left: 20px; width: 200px; top: 112px; }
  .card--back .wordmark__name { font-size: 31px; }
  .card--back .wordmark__sub { font-size: 10px; margin-top: 8px; letter-spacing: 2px; }

  .divider { position: absolute; left: 238px; top: 58px; width: 1px; height: 150px; background: var(--rule); }

  .contact { position: absolute; left: 269px; top: 56px; }
  .contact__name { font-family: "Oswald", Arial, sans-serif; font-weight: 500; font-size: 22px; color: var(--brand-red); line-height: 1.1; }
  .contact__title { font-size: 11.5px; color: var(--muted); margin-top: 3px; }
  .contact__list { list-style: none; margin-top: 22px; }
  .contact__list li {
    display: flex; align-items: center; gap: 9px; height: 16px;
    font-family: "Oswald", Arial, sans-serif; font-size: 12px; color: var(--ink);
  }
  .contact__list svg { width: 10px; height: 10px; fill: var(--brand-red); flex: none; }

  .back-footer { position: absolute; left: 0; bottom: 0; width: 484px; height: 38px; }
  .back-web { position: absolute; left: 270px; bottom: 12px; font-size: 12.5px; color: #fff; }
</style>
</head>
<body>

<section class="card card--front" aria-label="Card front">
  <div class="wordmark">
    <span class="wordmark__name">BRENWICK</span>
    <span class="wordmark__sub">CASING SERVICES</span>
  </div>
  <div class="services-band">
    <span>LAYDOWN MACHINE</span><span class="sep">|</span>
    <span>CASING CREW</span><span class="sep">|</span>
    <span>MUD TOOL</span><span class="sep">|</span>
    <span>TORQUE TURN</span>
  </div>
  <div class="front-web"><span class="dash"></span><span>www.brenwickcs.com</span><span class="dash"></span></div>
</section>

<section class="card card--back" aria-label="Card back">
  <div class="wordmark">
    <span class="wordmark__name">BRENWICK</span>
    <span class="wordmark__sub">CASING SERVICES</span>
  </div>
  <div class="divider"></div>
  <div class="contact">
    <div class="contact__name">Wade Harlan</div>
    <div class="contact__title">Area Manager</div>
    <ul class="contact__list">
      <li><svg viewBox="0 0 10 10" aria-hidden="true"><path d="M2 0.5 L3.6 2.6 L2.8 3.6 Q4 6 6.4 7.2 L7.4 6.4 L9.5 8 L8.4 9.5 Q3.5 9 0.5 1.6 Z"/></svg>(555) 214-6620</li>
      <li><svg viewBox="0 0 10 10" aria-hidden="true"><path d="M0.5 3.5 Q5 0 9.5 3.5 L8.2 4.6 L6.8 3.6 L6.8 2.8 Q5 2.2 3.2 2.8 L3.2 3.6 L1.8 4.6 Z M2 5 L8 5 L9 9 L1 9 Z"/></svg>(555) 318-4075</li>
      <li><svg viewBox="0 0 10 10" aria-hidden="true"><path d="M2.5 0.5 H7.5 V3 H2.5 Z M0.5 3.5 H9.5 V7.5 H8 V6 H2 V7.5 H0.5 Z M2.8 6.6 H7.2 V9.5 H2.8 Z"/></svg>(555) 214-6691</li>
      <li><svg viewBox="0 0 10 10" aria-hidden="true"><path d="M5 0.3 A3.4 3.4 0 0 1 8.4 3.7 Q8.4 6 5 9.7 Q1.6 6 1.6 3.7 A3.4 3.4 0 0 1 5 0.3 Z M5 2.4 A1.3 1.3 0 1 0 5 5 A1.3 1.3 0 1 0 5 2.4 Z"/></svg>Carver Flats, OK 73099</li>
      <li><svg viewBox="0 0 10 10" aria-hidden="true"><path d="M0.5 2 H9.5 L5 5.5 Z M0.5 3 L5 6.5 L9.5 3 V8.5 H0.5 Z"/></svg>wadeharlan@brenwickcs.com</li>
    </ul>
  </div>
  <svg class="back-footer" viewBox="0 0 484 38" preserveAspectRatio="none" aria-hidden="true">
    <rect x="0" y="19" width="220" height="19" fill="var(--slate)"/>
    <polygon points="218,0 484,0 484,38 196,38" fill="var(--brand-red)"/>
  </svg>
  <div class="back-web">www.brenwickcs.com</div>
</section>

</body>
</html>
```